Corvane Paintless Dent Removal

Our company works on vehicles removing dents using a highly skilled trade which the metal is massaged out with special tools without disturbing the original paint, hence paintless dent removal. Besides keeping the paint and metal original its also very environmentally friendly since no paint or toxic fillers are used. Also we we are one of the most experienced companies in the business with 25 years

Target Market(s)

Retail Automobile consumers, Auto Dealerships and Auto Body Shops

Industry/Entity Type

Auto Repair

Contact Information for Business Card

Dale Hollister
PO Box 518 Brookmere, NY 11962
631-555-0148
corvanepdr@mailbox-example.com
website corvanepdr.example
youtube corvane paintless dent removal
25 years of experience removing Dents, Dings and Hail Damage

Font styles to use
Serif
Sans Serif

Colors

Designer to choose colors to be used in the design.

Requirements
Must have
• I do like things that are simple but classy and somewhat bold, also I like my logo so that should be somewhat important

```html
<!DOCTYPE html>
<html lang="en">
<head>
<meta charset="utf-8">
<title>Corvane Paintless Dent Removal – Business Card</title>
<link href="https://fonts.googleapis.com/css2?family=Roboto:wght@400;500;700&family=Roboto+Condensed:wght@700&display=swap" rel="stylesheet">
<style>
  :root {
    --backdrop: #e8e5e1;
    --card-white: #f6f6f5;
    --navy: #13284b;
    --text-grey: #4a4a4a;
    --gold: #d7a92e;
    --badge-black: #111111;
    --white: #ffffff;
  }
  * { margin: 0; padding: 0; box-sizing: border-box; }
  html, body { width: 1200px; height: 960px; overflow: hidden; }
  body {
    position: relative;
    background: var(--backdrop);
    font-family: "Roboto", Arial, sans-serif;
  }
  .card {
    position: absolute;
    width: 600px;
    height: 343px;
    box-shadow: 0 3px 8px rgba(0,0,0,0.3);
  }
  .card-front { left: 314px; top: 113px; background: var(--card-white); }
  .card-back { left: 311px; top: 472px; background: var(--navy); }

  .brand-name {
    position: absolute;
    font-family: "Roboto", Arial, sans-serif;
    font-weight: 700;
    line-height: 1.05;
    text-align: center;
  }
  .card-front .brand-name {
    left: 40px; top: 48px; width: 276px;
    color: var(--navy);
    font-size: 34px;
  }
  .brand-name .brand-sub { display: block; font-size: 16px; letter-spacing: 0.3px; }

  .holder-name {
    position: absolute; left: 57px; top: 150px;
    font-family: "Roboto Condensed", "Arial Narrow", sans-serif;
    font-weight: 700; font-size: 21px;
    color: var(--navy);
  }
  .address {
    position: absolute; left: 57px; top: 181px;
    font-size: 14.5px; line-height: 19px; color: var(--text-grey);
  }
  .contact-list {
    position: absolute; left: 57px; top: 224px;
    list-style: none;
    font-size: 14.5px; color: var(--text-grey);
  }
  .contact-list li { display: flex; align-items: center; height: 19px; }
  .contact-list svg { width: 13px; height: 13px; margin-right: 9px; fill: var(--navy); }

  .years-seal { position: absolute; left: 461px; top: 213px; width: 82px; height: 82px; }

  .card-back .brand-name {
    left: 120px; top: 140px; width: 360px;
    color: var(--white);
    font-size: 40px;
  }
  .card-back .brand-name .brand-sub { font-size: 19px; }
  .back-web {
    position: absolute; left: 0; width: 100%; top: 280px;
    text-align: center; color: var(--white);
    font-size: 14px; letter-spacing: 4.6px;
  }
</style>
</head>
<body>
  <section class="card card-front">
    <div class="brand-name">CORVANE<span class="brand-sub">Paintless Dent Removal</span></div>
    <h1 class="holder-name">DALE HOLLISTER</h1>
    <p class="address">PO Box 518<br>Brookmere, NY 11962</p>
    <ul class="contact-list">
      <li><svg viewBox="0 0 24 24"><path d="M6.6 10.8a15 15 0 0 0 6.6 6.6l2.2-2.2c.3-.3.7-.4 1-.2 1.1.4 2.3.6 3.6.6.6 0 1 .4 1 1V20c0 .6-.4 1-1 1A17 17 0 0 1 3 4c0-.6.4-1 1-1h3.5c.6 0 1 .4 1 1 0 1.3.2 2.5.6 3.6.1.3 0 .7-.2 1z"/></svg>631-555-0148</li>
      <li><svg viewBox="0 0 24 24"><path d="M2 5h20v14H2z M4 7v.5l8 5 8-5V7l-8 5z" fill-rule="evenodd"/></svg>corvanepdr@mailbox-example.com</li>
      <li><svg viewBox="0 0 24 24"><circle cx="12" cy="12" r="10"/><path d="M2 12h20M12 2c3 3 3 17 0 20M12 2c-3 3-3 17 0 20" stroke="#f6f6f5" stroke-width="1.6" fill="none"/></svg>corvanepdr.example</li>
      <li><svg viewBox="0 0 24 24"><rect x="2" y="5" width="20" height="14" rx="3"/></svg>corvane paintless dent removal</li>
    </ul>
    <svg class="years-seal" viewBox="0 0 82 82" role="img" aria-label="25 years of experience seal">
      <circle cx="41" cy="41" r="40" fill="var(--gold)"/>
      <circle cx="41" cy="41" r="27" fill="var(--badge-black)"/>
      <text x="41" y="47" text-anchor="middle" font-family="Roboto Condensed, sans-serif" font-weight="700" font-size="24" fill="var(--gold)">25</text>
      <text x="41" y="58" text-anchor="middle" font-family="Roboto Condensed, sans-serif" font-weight="700" font-size="9" fill="var(--gold)">YEARS</text>
    </svg>
  </section>

  <section class="card card-back">
    <div class="brand-name">CORVANE<span class="brand-sub">Paintless Dent Removal</span></div>
    <p class="back-web">www.corvanepdr.example</p>
  </section>
</body>
</html>
```